New Alcoholic Spiked Seltzer Line

We need a can design for a line of low calorie alcoholic seltzer. This product is a sparkling water and vodka drink with no sugar added in a slim 12 oz can.

This is a lighter, healthier, alternative to the sugary ready-to-drinks on the market. The product contains only 3 ingredients: Vodka, Water and Natural Flavors. It has only 100 calories but still has 5% alcohol, so you don't need to sacrifice alcohol to cut calories.

This product also does not contain any preservatives.

We want this design to communicate the following objectives to the consumer and in this order:

1. Appetizing product
2.Low calorie
3.Communicate the type of beverage (Spiked Seltzer)

The brand name of the product is VELKA.

The flavor of the product needed to be used for the design is Mango-Orange.

Comparable products are:

www.brindlefizzworks.example/
https://www.quorvabubbles.example
https://pelnavo.example/

The designs should not infringe or copy the creative directions of the products mentionned above. They are only given so that you can better understand the type of product we are developing.

Target Market(s)

Young Professional women between the ages of 25 and 44

Industry/Entity Type

Product

Colors

Designer to choose colors to be used in the design.

Requirements
Must have
• Design extendibility, meaning it can be adapted for other flavors.
• This is a new category in the market we are targeting, so consumers must easily be able to identify what type of product this is.

```html
<!DOCTYPE html>
<html lang="en">
<head>
<meta charset="UTF-8">
<title>VELKA Spiked Seltzer – Mango-Orange Can Label</title>
<link rel="stylesheet" href="https://fonts.googleapis.com/css2?family=Montserrat:wght@400;500;700;800&display=swap">
<style>
  :root {
    --backdrop: #5f93cc;
    --label-white: #ffffff;
    --lime: #b9d43a;
    --sun-yellow: #f4d83a;
    --mango-orange: #f08a3c;
    --berry-pink: #e9386f;
    --badge-red: #d41920;
    --ink-white: #ffffff;
    --ink-berry: #c8285c;
  }
  html, body {
    margin: 0;
    padding: 0;
    width: 1200px;
    height: 1200px;
    overflow: hidden;
    background: var(--backdrop);
  }
  .canvas {
    width: 1200px;
    height: 1200px;
    display: flex;
    align-items: center;
    justify-content: center;
  }
  .can-label {
    width: 440px;
    height: 1000px;
    display: block;
    background: var(--label-white);
    font-family: "Montserrat", sans-serif;
  }
  .stop-lime { stop-color: var(--lime); }
  .stop-yellow { stop-color: var(--sun-yellow); }
  .stop-orange { stop-color: var(--mango-orange); }
  .stop-pink { stop-color: var(--berry-pink); }
  .category-line { fill: var(--ink-berry); font-weight: 700; text-anchor: middle; letter-spacing: 5px; }
  .calorie-badge { fill: var(--badge-red); }
  .badge-text { fill: var(--ink-white); font-weight: 500; text-anchor: middle; }
  .badge-number { fill: var(--ink-white); font-weight: 400; text-anchor: middle; }
  .brand-name { fill: var(--ink-white); font-weight: 800; text-anchor: middle; }
  .ingredients { fill: var(--ink-white); font-weight: 400; text-anchor: middle; }
  .flavor-name { fill: var(--ink-white); font-weight: 700; text-anchor: middle; letter-spacing: 2px; }
  .abv { fill: var(--ink-white); font-weight: 400; text-anchor: middle; }
</style>
</head>
<body>
<main class="canvas">
  <svg class="can-label" viewBox="0 0 440 1000" xmlns="http://www.w3.org/2000/svg" aria-label="VELKA Mango-Orange spiked seltzer can label">
    <defs>
      <linearGradient id="flavor-fade" x1="0" y1="0" x2="0" y2="1">
        <stop class="stop-lime" offset="0"/>
        <stop class="stop-yellow" offset="0.38"/>
        <stop class="stop-orange" offset="0.62"/>
        <stop class="stop-pink" offset="1"/>
      </linearGradient>
    </defs>

    <text class="category-line" x="220" y="95" font-size="20">SPIKED SELTZER</text>

    <rect class="flavor-capsule" x="30" y="130" width="380" height="840" rx="190" fill="url(#flavor-fade)"/>

    <g class="calorie-badge-group">
      <circle class="calorie-badge" cx="318" cy="205" r="68"/>
      <text class="badge-text" x="318" y="175" font-size="21">only</text>
      <text class="badge-number" x="318" y="220" font-size="46">100</text>
      <text class="badge-text" x="318" y="250" font-size="21">calories</text>
    </g>

    <text class="brand-name" transform="translate(272,560) rotate(-90)" font-size="150" textLength="540" lengthAdjust="spacingAndGlyphs">VELKA</text>
    <text class="ingredients" transform="translate(362,560) rotate(-90)" font-size="26">Vodka, Water and Natural Flavors</text>

    <text class="flavor-name" x="220" y="888" font-size="24">MANGO-ORANGE</text>
    <text class="abv" x="220" y="928" font-size="24">5% alcohol</text>
  </svg>
</main>
</body>
</html>
```